World travel poster - I want to remember where I've been!

I would like a poster for me to print and keep in my home as a record of my world travels. It must look like a mechanical sign in an airport (see picture for example) However I am flexible with exact layout, if you'd like to add images used to enhance poster etc. I have also uploaded some pictures from my travels if you would like to use some or all of them. They are named according to location.

Poster must include:
USA 2003
Malaysia 2006
Thailand 2007
Italy 2009
India, Vietnam, Hong Kong 2010
Bali 2011
Malaysia 2012
Singapore 2012
Vietnam, Cambodia, Laos 2013
Europe 2015

and the quote:

"The world is a book and those who do not travel read only one page."
― Severin of Caldra
Updates

Hi there. I have uploaded some photos of my travels to possibly use in my poster. They are named according to location. I haven't decided if I prefer the originial layout or with images, so please post both for me to consider. Thanks so much for your time to consider my project.

Target Market(s)

Something to catch the eye of visitors and remind me of my adventures.
A classic piece that is a conversation starter.

Industry/Entity Type

Airport

Font styles to use
Other font styles liked:
• Airport mechanical font

Requirements
Must have
• Some lettering like a mechanical airport board (see image attached for example).
Dimensions that are easy to print - either A3, or a long/narrow poster.
Nice to have
• A splash of colour or an image, maybe the words 'arrivals' or 'departures'

Use of some of my pictures if it doesn't look too busy.
Should not have
• Anything too over the top.

```html
<!DOCTYPE html>
<html lang="en">
<head>
<meta charset="utf-8">
<title>Departures — Travel Record Poster</title>
<link rel="stylesheet" href="https://fonts.googleapis.com/css2?family=Montserrat:wght@700&family=Oswald:wght@500&family=Open+Sans:wght@300;400;700&display=swap">
<style>
  :root {
    --board-bg: #2a2a2a;
    --tile-top: #3c3c3c;
    --tile-bottom: #1c1c1c;
    --tile-split: #0d0d0d;
    --tile-edge: #4a4a4a;
    --letter: #f4f4f4;
    --accent: #f5c400;
    --quote: #e8e8e8;
    --credit: #bdbdbd;
  }
  * { box-sizing: border-box; margin: 0; padding: 0; }
  html, body { width: 836px; height: 1200px; overflow: hidden; background: var(--board-bg); }
  .poster {
    position: relative;
    width: 836px;
    height: 1200px;
    overflow: hidden;
    background: var(--board-bg);
  }
  .header {
    position: absolute;
    left: 28px;
    top: 30px;
    display: flex;
    align-items: center;
    gap: 22px;
  }
  .header__icon { width: 56px; height: 34px; }
  .header__title {
    font-family: "Montserrat", sans-serif;
    font-weight: 700;
    font-size: 38px;
    letter-spacing: 5px;
    color: var(--accent);
  }
  .board {
    position: absolute;
    left: 28px;
    top: 112px;
    display: flex;
    flex-direction: column;
    gap: 15px;
  }
  .board__row {
    display: flex;
    align-items: center;
    gap: 5px;
    height: 51px;
  }
  .tile {
    position: relative;
    width: 40px;
    height: 51px;
    border-radius: 3px;
    background: linear-gradient(to bottom, var(--tile-top) 0%, #303030 49%, var(--tile-bottom) 51%, #262626 100%);
    box-shadow: inset 0 0 0 1px var(--tile-edge), 0 2px 2px rgba(0,0,0,0.5);
    font-family: "Oswald", sans-serif;
    font-weight: 500;
    font-size: 36px;
    line-height: 51px;
    text-align: center;
    color: var(--letter);
  }
  .tile::after {
    content: "";
    position: absolute;
    left: 0;
    right: 0;
    top: 50%;
    height: 2px;
    margin-top: -1px;
    background: var(--tile-split);
  }
  .tile--digit { color: var(--accent); }
  .flag {
    width: 88px;
    height: 54px;
    margin-left: 6px;
    display: block;
    box-shadow: 0 2px 3px rgba(0,0,0,0.5);
  }
  .flag + .flag { margin-left: 14px; }
  .quote {
    position: absolute;
    left: 28px;
    top: 930px;
    font-family: "Open Sans", sans-serif;
    font-weight: 300;
    font-size: 54px;
    line-height: 62px;
    color: var(--quote);
  }
  .quote__emphasis { font-weight: 700; color: var(--accent); }
  .quote__credit {
    position: absolute;
    left: 28px;
    top: 1128px;
    font-family: "Open Sans", sans-serif;
    font-weight: 400;
    font-size: 22px;
    color: var(--credit);
  }
</style>
</head>
<body>
<main class="poster">
  <header class="header">
    <svg class="header__icon" viewBox="0 0 56 34" aria-hidden="true">
      <path fill="#f5c400" d="M2 22 L8 22 L13 16 L26 17 L18 4 L24 4 L36 17 L48 17 C54 17 55 21 48 22 L36 23 L24 33 L18 33 L25 23 L13 24 L8 28 L2 28 Z"/>
    </svg>
    <h1 class="header__title">DEPARTURES</h1>
  </header>

  <section class="board" aria-label="Travel destinations">
    <div class="board__row">
      <span class="tile">U</span><span class="tile">S</span><span class="tile">A</span><span class="tile">–</span><span class="tile tile--digit">2</span><span class="tile tile--digit">0</span><span class="tile tile--digit">0</span><span class="tile tile--digit">3</span>
      <svg class="flag" viewBox="0 0 76 52" role="img" aria-label="USA flag">
        <rect width="76" height="52" fill="#fff"/>
        <g fill="#c8102e"><rect y="0" width="76" height="4"/><rect y="8" width="76" height="4"/><rect y="16" width="76" height="4"/><rect y="24" width="76" height="4"/><rect y="32" width="76" height="4"/><rect y="40" width="76" height="4"/><rect y="48" width="76" height="4"/></g>
        <rect width="32" height="28" fill="#1f2f6b"/>
      </svg>
    </div>

    <div class="board__row">
      <span class="tile">M</span><span class="tile">A</span><span class="tile">L</span><span class="tile">A</span><span class="tile">Y</span><span class="tile">S</span><span class="tile">I</span><span class="tile">A</span><span class="tile">–</span><span class="tile tile--digit">2</span><span class="tile tile--digit">0</span><span class="tile tile--digit">0</span><span class="tile tile--digit">6</span>
      <svg class="flag" viewBox="0 0 76 52" role="img" aria-label="Malaysia flag">
        <rect width="76" height="52" fill="#fff"/>
        <g fill="#cc0001"><rect y="0" width="76" height="4"/><rect y="8" width="76" height="4"/><rect y="16" width="76" height="4"/><rect y="24" width="76" height="4"/><rect y="32" width="76" height="4"/><rect y="40" width="76" height="4"/><rect y="48" width="76" height="4"/></g>
        <rect width="38" height="28" fill="#010066"/>
        <circle cx="15" cy="14" r="8" fill="#fc0"/><circle cx="18" cy="14" r="7" fill="#010066"/><circle cx="28" cy="14" r="4" fill="#fc0"/>
      </svg>
    </div>

    <div class="board__row">
      <span class="tile">T</span><span class="tile">H</span><span class="tile">A</span><span class="tile">I</span><span class="tile">L</span><span class="tile">A</span><span class="tile">N</span><span class="tile">D</span><span class="tile">–</span><span class="tile tile--digit">2</span><span class="tile tile--digit">0</span><span class="tile tile--digit">0</span><span class="tile tile--digit">7</span>
      <svg class="flag" viewBox="0 0 60 36" role="img" aria-label="Thailand flag">
        <rect width="60" height="36" fill="#a51931"/>
        <rect y="6" width="60" height="24" fill="#f4f5f8"/>
        <rect y="12" width="60" height="12" fill="#2d2a4a"/>
      </svg>
    </div>

    <div class="board__row">
      <span class="tile">I</span><span class="tile">T</span><span class="tile">A</span><span class="tile">L</span><span class="tile">Y</span><span class="tile">–</span><span class="tile tile--digit">2</span><span class="tile tile--digit">0</span><span class="tile tile--digit">0</span><span class="tile tile--digit">9</span>
      <svg class="flag" viewBox="0 0 3 2" role="img" aria-label="Italy flag">
        <rect width="1" height="2" fill="#009246"/><rect x="1" width="1" height="2" fill="#fff"/><rect x="2" width="1" height="2" fill="#ce2b37"/>
      </svg>
    </div>

    <div class="board__row">
      <span class="tile">I</span><span class="tile">N</span><span class="tile">D</span><span class="tile">I</span><span class="tile">A</span><span class="tile">,</span><span class="tile">V</span><span class="tile">I</span><span class="tile">E</span><span class="tile">T</span><span class="tile">N</span><span class="tile">A</span><span class="tile">M</span>
      <svg class="flag" viewBox="0 0 60 36" role="img" aria-label="India flag">
        <rect width="60" height="12" fill="#ff9933"/><rect y="12" width="60" height="12" fill="#fff"/><rect y="24" width="60" height="12" fill="#138808"/>
        <circle cx="30" cy="18" r="4.5" fill="none" stroke="#000080" stroke-width="1"/>
      </svg>
      <svg class="flag" viewBox="0 0 60 36" role="img" aria-label="Vietnam flag">
        <rect width="60" height="36" fill="#da251d"/>
        <polygon fill="#ffcd00" points="30,7 32.6,15 41,15 34.2,20 36.8,28 30,23 23.2,28 25.8,20 19,15 27.4,15"/>
      </svg>
    </div>

    <div class="board__row">
      <span class="tile">&amp;</span><span class="tile">–</span><span class="tile">H</span><span class="tile">O</span><span class="tile">N</span><span class="tile">G</span><span class="tile">K</span><span class="tile">O</span><span class="tile">N</span><span class="tile">G</span><span class="tile">–</span><span class="tile tile--digit">2</span><span class="tile tile--digit">0</span><span class="tile tile--digit">1</span><span class="tile tile--digit">0</span>
      <svg class="flag" viewBox="0 0 60 36" role="img" aria-label="Hong Kong flag">
        <rect width="60" height="36" fill="#de2910"/>
        <circle cx="30" cy="18" r="9" fill="#fff"/>
      </svg>
    </div>

    <div class="board__row">
      <span class="tile">B</span><span class="tile">A</span><span class="tile">L</span><span class="tile">I</span><span class="tile">–</span><span class="tile tile--digit">2</span><span class="tile tile--digit">0</span><span class="tile tile--digit">1</span><span class="tile tile--digit">1</span>
      <svg class="flag" viewBox="0 0 60 36" role="img" aria-label="Bali provincial flag">
        <rect width="60" height="36" fill="#f0a020"/>
      </svg>
    </div>

    <div class="board__row">
      <span class="tile">M</span><span class="tile">A</span><span class="tile">L</span><span class="tile">A</span><span class="tile">Y</span><span class="tile">S</span><span class="tile">I</span><span class="tile">A</span><span class="tile">–</span><span class="tile tile--digit">2</span><span class="tile tile--digit">0</span><span class="tile tile--digit">1</span><span class="tile tile--digit">2</span>
      <svg class="flag" viewBox="0 0 76 52" role="img" aria-label="Malaysia flag">
        <rect width="76" height="52" fill="#fff"/>
        <g fill="#cc0001"><rect y="0" width="76" height="4"/><rect y="8" width="76" height="4"/><rect y="16" width="76" height="4"/><rect y="24" width="76" height="4"/><rect y="32" width="76" height="4"/><rect y="40" width="76" height="4"/><rect y="48" width="76" height="4"/></g>
        <rect width="38" height="28" fill="#010066"/>
        <circle cx="15" cy="14" r="8" fill="#fc0"/><circle cx="18" cy="14" r="7" fill="#010066"/><circle cx="28" cy="14" r="4" fill="#fc0"/>
      </svg>
    </div>

    <div class="board__row">
      <span class="tile">S</span><span class="tile">I</span><span class="tile">N</span><span class="tile">G</span><span class="tile">A</span><span class="tile">P</span><span class="tile">O</span><span class="tile">R</span><span class="tile">E</span><span class="tile">–</span><span class="tile tile--digit">2</span><span class="tile tile--digit">0</span><span class="tile tile--digit">1</span><span class="tile tile--digit">2</span>
      <svg class="flag" viewBox="0 0 60 36" role="img" aria-label="Singapore flag">
        <rect width="60" height="18" fill="#ef3340"/><rect y="18" width="60" height="18" fill="#fff"/>
        <circle cx="11" cy="9" r="5" fill="#fff"/><circle cx="13" cy="9" r="4.5" fill="#ef3340"/>
      </svg>
    </div>

    <div class="board__row">
      <span class="tile">V</span><span class="tile">I</span><span class="tile">E</span><span class="tile">T</span><span class="tile">N</span><span class="tile">A</span><span class="tile">M</span><span class="tile">,</span><span class="tile">L</span><span class="tile">A</span><span class="tile">O</span><span class="tile">S</span>
      <svg class="flag" viewBox="0 0 60 36" role="img" aria-label="Vietnam flag">
        <rect width="60" height="36" fill="#da251d"/>
        <polygon fill="#ffcd00" points="30,7 32.6,15 41,15 34.2,20 36.8,28 30,23 23.2,28 25.8,20 19,15 27.4,15"/>
      </svg>
      <svg class="flag" viewBox="0 0 60 36" role="img" aria-label="Laos flag">
        <rect width="60" height="36" fill="#ce1126"/><rect y="9" width="60" height="18" fill="#002868"/>
        <circle cx="30" cy="18" r="7" fill="#fff"/>
      </svg>
    </div>

    <div class="board__row">
      <span class="tile">&amp;</span><span class="tile">–</span><span class="tile">C</span><span class="tile">A</span><span class="tile">M</span><span class="tile">B</span><span class="tile">O</span><span class="tile">D</span><span class="tile">I</span><span class="tile">A</span><span class="tile">–</span><span class="tile tile--digit">2</span><span class="tile tile--digit">0</span><span class="tile tile--digit">1</span><span class="tile tile--digit">3</span>
      <svg class="flag" viewBox="0 0 60 36" role="img" aria-label="Cambodia flag">
        <rect width="60" height="36" fill="#032ea1"/><rect y="9" width="60" height="18" fill="#e00025"/>
      </svg>
    </div>

    <div class="board__row">
      <span class="tile">E</span><span class="tile">U</span><span class="tile">R</span><span class="tile">O</span><span class="tile">P</span><span class="tile">E</span><span class="tile">–</span><span class="tile tile--digit">2</span><span class="tile tile--digit">0</span><span class="tile tile--digit">1</span><span class="tile tile--digit">5</span>
      <svg class="flag" viewBox="0 0 60 36" role="img" aria-label="European flag">
        <rect width="60" height="36" fill="#003399"/>
        <g fill="#ffcc00">
          <circle cx="30" cy="8" r="1.4"/><circle cx="35" cy="9.3" r="1.4"/><circle cx="38.7" cy="13" r="1.4"/><circle cx="40" cy="18" r="1.4"/><circle cx="38.7" cy="23" r="1.4"/><circle cx="35" cy="26.7" r="1.4"/>
          <circle cx="30" cy="28" r="1.4"/><circle cx="25" cy="26.7" r="1.4"/><circle cx="21.3" cy="23" r="1.4"/><circle cx="20" cy="18" r="1.4"/><circle cx="21.3" cy="13" r="1.4"/><circle cx="25" cy="9.3" r="1.4"/>
        </g>
      </svg>
    </div>
  </section>

  <blockquote class="quote">
    The world is a book and<br>
    those who do not travel read<br>
    <span class="quote__emphasis">only one page.</span>
  </blockquote>
  <p class="quote__credit">- Severin of Caldra</p>
</main>
</body>
</html>
```